Verodex business card

Business card for sustainable investment company called "Verodex". Verodex is an exchange platform selling carbon credits between buyers and sellers. Carbon Credits are an environmental commodity for reducing global carbon emissions.

the card should obviously have our logo and the theme should be sustainability/environment mixed with a trading platform.

Contact Information for Business Card

Logo, Name, Title, Phone, Email

Colors
0054AA
0677BA
7BADD7
CADEEF
E8F1F8
0094D4
00A9DD
6FCCEA
C7EBF8
E9F6FB
00AB8E
00BBA5
67D7C9
C6EFE9
E9F9F6
59FF00
82FF00
B8FF75
E3FFCB
F4FFEA

```html
<!DOCTYPE html>
<html lang="en">
<head>
<meta charset="utf-8">
<title>Verodex business card</title>
<link href="https://fonts.googleapis.com/css2?family=Montserrat+Alternates:wght@400;500;600;700&display=swap" rel="stylesheet">
<style>
  :root {
    --bg: #e4e6e9;
    --navy: #1f3550;
    --blue-deep: #0054AA;
    --blue: #0677BA;
    --blue-soft: #7BADD7;
    --cyan: #6FCCEA;
    --teal-light: #67D7C9;
    --card-white: #f2f3f4;
    --ink: #1f2a3a;
  }
  * { margin: 0; padding: 0; box-sizing: border-box; }
  html, body { width: 1200px; height: 1200px; overflow: hidden; }
  body {
    background: var(--bg);
    font-family: "Montserrat Alternates", sans-serif;
    position: relative;
  }
  .card {
    position: absolute;
    left: 170px;
    width: 860px;
    height: 491px;
    border-radius: 28px;
    overflow: hidden;
    box-shadow: 0 10px 30px rgba(0,0,0,0.12);
  }
  .card-front {
    top: 80px;
    background: linear-gradient(200deg, #66ccda 0%, #5aa9cf 55%, #5b8fc9 80%, #86c2dc 100%);
  }
  .front-decoration {
    position: absolute;
    left: 40px; top: 0;
    width: 420px; height: 491px;
    background: linear-gradient(135deg, rgba(123,173,215,0.55), rgba(0,84,170,0.18));
  }
  .front-brand {
    position: absolute;
    left: 250px; top: 205px;
    display: flex; align-items: center; gap: 24px;
    color: #ffffff;
  }
  .brand-mark { width: 62px; height: 62px; background: currentColor; }
  .brand-name {
    font-weight: 600;
    font-size: 64px;
    letter-spacing: 2px;
    line-height: 1;
  }
  .card-back {
    top: 630px;
    background: linear-gradient(160deg, #f4f5f6 0%, #e9eaeb 100%);
  }
  .back-brand {
    position: absolute;
    left: 85px; top: 236px;
    display: flex; align-items: center; gap: 18px;
    color: var(--navy);
  }
  .back-brand .brand-mark { width: 44px; height: 44px; background: var(--blue-soft); }
  .back-brand .brand-name { font-size: 44px; }
  .contact-block {
    position: absolute;
    left: 430px; top: 120px;
    right: 0;
    color: var(--ink);
  }
  .person-name {
    font-weight: 700;
    font-size: 38px;
    color: var(--blue);
    line-height: 1.1;
  }
  .person-title { font-size: 19px; margin-top: 4px; }
  .divider {
    height: 2px;
    margin: 12px 0 16px;
    background: linear-gradient(90deg, var(--cyan), var(--blue-deep));
  }
  .office-name { font-weight: 700; font-size: 19px; }
  .office-address { font-size: 19px; margin-top: 2px; }
  .contact-list { list-style: none; margin-top: 18px; }
  .contact-list li {
    display: flex; align-items: center; gap: 10px;
    font-size: 19px; margin-bottom: 6px;
  }
  .contact-list svg { width: 18px; height: 18px; flex: none; }
</style>
</head>
<body>
  <section class="card card-front" aria-label="Card front">
    <div class="front-decoration" role="img" aria-label="Faint large brand symbol decoration"></div>
    <div class="front-brand">
      <span class="brand-mark"></span>
      <span class="brand-name">VERODEX</span>
    </div>
  </section>

  <section class="card card-back" aria-label="Card back">
    <div class="back-brand">
      <span class="brand-mark"></span>
      <span class="brand-name">VERODEX</span>
    </div>
    <div class="contact-block">
      <h1 class="person-name">Milan Kovary</h1>
      <p class="person-title">Sales Representative</p>
      <div class="divider"></div>
      <p class="office-name">Verodex Head Office</p>
      <p class="office-address">Budapest XI. Lenke utca 14.</p>
      <ul class="contact-list">
        <li>
          <svg viewBox="0 0 24 24"><path fill="#0677BA" d="M6.6 10.8a15 15 0 0 0 6.6 6.6l2.2-2.2a1 1 0 0 1 1-.25 11.4 11.4 0 0 0 3.6.57 1 1 0 0 1 1 1V20a1 1 0 0 1-1 1A17 17 0 0 1 3 4a1 1 0 0 1 1-1h3.5a1 1 0 0 1 1 1c0 1.25.2 2.45.57 3.57a1 1 0 0 1-.25 1z"/></svg>
          +36 30 555 0142
        </li>
        <li>
          <svg viewBox="0 0 24 24"><rect x="2" y="5" width="20" height="14" rx="2" fill="#0677BA"/><path d="M3 6l9 7 9-7" fill="none" stroke="#f2f3f4" stroke-width="1.6"/></svg>
          szerviz@verodex.com
        </li>
        <li>
          <svg viewBox="0 0 24 24" fill="none" stroke="#0677BA" stroke-width="2"><circle cx="12" cy="12" r="9"/><path d="M3 12h18M12 3c3 3.5 3 14.5 0 18M12 3c-3 3.5-3 14.5 0 18"/></svg>
          www.verodex.com
        </li>
      </ul>
    </div>
  </section>
</body>
</html>
```